Veltrane Group Business Card Design

The CEO is looking for a new trendy look for his business card.
You can stay with current branding or come up with something new/creative. It can be 3D, including Medical Office buildings. You can use our logo in a variety of colors. Please include name, title, company name, company website, email address, cell number

Target Market(s)

Real Estate Development and Construction

Industry/Entity Type

Health care real estate

Contact Information for Business Card

Rohesh Kamdar, CEO M-604.781.2249 E-roheshkamdar@veltrane.com Address:4180 Lindqvist Ave, Tampa, FL 33482 www.veltrane.com

Font styles to use
Other font styles liked:
• Be creative

Requirements
Must have
• Creative, trendy look
Nice to have
• Please go to our website to get a feel- www. veltrane.com
Should not have
• small fonts

```html
<!DOCTYPE html>
<html lang="en">
<head>
<meta charset="utf-8">
<title>Veltrane Group Business Card</title>
<link rel="stylesheet" href="https://fonts.googleapis.com/css2?family=Montserrat:wght@400;500;700;800;900&display=swap">
<style>
  :root {
    --stage: #2b2e33;
    --card-black: #0d0d0e;
    --card-white: #ffffff;
    --ink-white: #f2f2f2;
    --ink-grey: #a9a9a9;
    --ink-black: #0d0d0e;
    --gloss: #1d1d1f;
    --arc: #2a2a2c;
  }
  * { box-sizing: border-box; margin: 0; padding: 0; }
  html, body { width: 1200px; height: 900px; overflow: hidden; }
  body {
    background: var(--stage);
    font-family: "Montserrat", sans-serif;
    position: relative;
  }
  .card {
    position: absolute;
    left: 300px;
    width: 600px;
    height: 343px;
    border-radius: 28px;
    overflow: hidden;
    background: var(--card-black);
    box-shadow: 0 14px 30px rgba(0,0,0,0.45);
  }
  .card--front { top: 92px; }
  .card--back { top: 467px; }

  .front-shape { position: absolute; inset: 0; }

  .identity { position: absolute; left: 40px; top: 38px; }
  .identity__name {
    color: var(--ink-white);
    font-size: 24px;
    font-weight: 700;
    letter-spacing: 0.2px;
  }
  .identity__title {
    color: var(--ink-grey);
    font-size: 13px;
    font-weight: 500;
    margin-top: 3px;
  }
  .address {
    position: absolute;
    left: 40px;
    top: 130px;
    color: var(--ink-grey);
    font-size: 14px;
    line-height: 1.45;
  }
  .contacts {
    position: absolute;
    left: 40px;
    top: 196px;
    list-style: none;
    color: var(--ink-white);
    font-size: 14px;
    line-height: 1;
  }
  .contacts li { display: flex; align-items: center; gap: 10px; margin-bottom: 11px; }
  .contacts svg { width: 14px; height: 14px; flex: none; }

  .brand {
    position: absolute;
    left: 380px;
    top: 150px;
    color: var(--ink-black);
    font-size: 28px;
    font-weight: 800;
    line-height: 1;
    letter-spacing: -0.5px;
  }
  .brand__mark {
    display: inline-block;
    width: 14px; height: 14px;
    background: var(--ink-black);
    margin-right: 8px;
    vertical-align: 2px;
  }
  .brand--back {
    left: 0; right: 0; top: 148px;
    text-align: center;
    color: var(--gloss);
    font-size: 44px;
  }
  .brand--back .brand__mark { background: var(--gloss); width: 20px; height: 20px; vertical-align: 4px; margin-right: 12px; }
</style>
</head>
<body>
  <section class="card card--front" aria-label="Business card front">
    <svg class="front-shape" viewBox="0 0 600 343" aria-hidden="true">
      <path d="M600 0 L560 0 C440 30 340 110 340 215 C340 290 380 330 420 343 L600 343 Z" fill="var(--card-white)"/>
      <path d="M520 10 C410 45 330 120 326 215 C323 275 345 315 370 343" fill="none" stroke="var(--arc)" stroke-width="5" stroke-linecap="round"/>
    </svg>

    <div class="identity">
      <h1 class="identity__name">Rohesh Kamdar</h1>
      <p class="identity__title">CEO</p>
    </div>

    <p class="address">4180 Lindqvist Ave,<br>Tampa, FL 33482</p>

    <ul class="contacts">
      <li>
        <svg viewBox="0 0 16 16"><path d="M4 1.5 L6.5 4.5 L5 6.2 C6 8.3 7.7 10 9.8 11 L11.5 9.5 L14.5 12 L12.8 14.3 C7 13.6 2.4 9 1.7 3.2 Z" fill="var(--ink-white)"/></svg>
        <span>604.781.2249</span>
      </li>
      <li>
        <svg viewBox="0 0 16 16"><rect x="1" y="3.5" width="14" height="9" rx="1" fill="var(--ink-white)"/><path d="M1.5 4 L8 9 L14.5 4" fill="none" stroke="var(--card-black)" stroke-width="1.3"/></svg>
        <span>roheshkamdar@veltrane.com</span>
      </li>
      <li>
        <svg viewBox="0 0 16 16"><circle cx="8" cy="8" r="6.5" fill="none" stroke="var(--ink-white)" stroke-width="1.4"/><ellipse cx="8" cy="8" rx="2.8" ry="6.5" fill="none" stroke="var(--ink-white)" stroke-width="1.2"/><line x1="1.5" y1="8" x2="14.5" y2="8" stroke="var(--ink-white)" stroke-width="1.2"/></svg>
        <span>www.veltrane.com</span>
      </li>
    </ul>

    <p class="brand"><span class="brand__mark"></span>Veltrane Group</p>
  </section>

  <section class="card card--back" aria-label="Business card back">
    <p class="brand brand--back"><span class="brand__mark"></span>Veltrane Group</p>
  </section>
</body>
</html>
```